Law Firm Website

We are a small California based law firm specializing in business, corporate and litigation matters. We need to have our website redesigned. We are looking for a new and fresh look for our site, keeping in mind that we are a law firm.
What we don't want:
**the traditional "gavel" and "scales of justice" look
**anything too crazy
What we do want:
**sophisticated yet modern and fresh corporate look and feel
**samples of websites we really like:
http://www.tarnwellhope.example
http://www.marrowgate.example/
we also like:
http://www.fenwoodastley.example/
http://www.qz.example/
http://www.brenhollow.example/
http://www.pvdn.example
http://www.nqrlaw.example/
The content will be whatever is currently on our website (www.okabelawgroup.example). We will be selecting the winner based on originality and keeping the above requirements in mind. Please note that the photos that you use will be the ones that we will be using, so choose wisely because the photos will make a difference.
Target Market(s)
Corporate clients
Industry/Entity Type
Law Firm
Look and feel

```html
<!DOCTYPE html>
<html lang="en">
<head>
<meta charset="utf-8">
<title>Okabe Law Group, LLP — Attorneys at Law</title>
<link rel="stylesheet" href="https://fonts.googleapis.com/css2?family=Signika:wght@300;400;600&family=Oxygen:wght@400&family=Arimo:wght@400;700&display=swap">
<style>
  :root {
    --ink-dark: #141414;
    --blue: #0b6fc4;
    --blue-light: #1b8fe2;
    --blue-deep: #0762b3;
    --text: #555;
    --text-soft: #666;
    --rule: #dcdcdc;
    --white: #fff;
  }
  * { box-sizing: border-box; margin: 0; padding: 0; }
  html, body { width: 988px; height: 1200px; overflow: hidden; }
  body {
    position: relative;
    font-family: "Oxygen", sans-serif;
    color: var(--text);
    background: linear-gradient(#cfcfcf 469px, #e2e2e2 700px, #f2f2f2 1200px);
  }
  .top-band { position: absolute; left: 0; top: 0; width: 988px; height: 469px; background: var(--ink-dark); }
  .abs { position: absolute; }

  .brand { left: 79px; top: 17px; width: 210px; text-align: center; }
  .brand-mark { display: block; width: 65px; height: 65px; margin: 0 auto; background: linear-gradient(135deg, #4fb2f0, #0c6cc2); }
  .brand-name { font-family: "Signika", sans-serif; font-weight: 300; color: var(--white); font-size: 21px; margin-top: 4px; white-space: nowrap; }
  .brand-tag { font-family: "Arimo", sans-serif; color: #ddd; font-size: 11px; margin-top: 0; }

  .call { right: 114px; top: 20px; text-align: right; font-family: "Signika", sans-serif; font-weight: 300; color: var(--white); white-space: nowrap; }
  .call-label { font-size: 15px; }
  .call-number { font-size: 19px; margin-top: 1px; }
  .call-icon { left: 882px; top: 27px; }

  .search { left: 735px; top: 78px; width: 169px; height: 28px; background: #f2f2f2; border: 1px solid #ccc; font-family: "Signika", sans-serif; font-weight: 300; font-size: 12px; color: #333; padding: 6px 10px; }
  .search svg { position: absolute; right: 5px; top: 5px; }
  .search::after { content: ""; position: absolute; right: 26px; top: 4px; width: 1px; height: 18px; background: #ccc; }

  .nav { left: 79px; top: 137px; width: 825px; height: 43px; background: linear-gradient(var(--blue-light), var(--blue-deep)); display: flex; }
  .nav a { color: var(--white); text-decoration: none; font-family: "Arimo", sans-serif; font-weight: 700; font-size: 11.5px; display: flex; align-items: center; justify-content: center; border-right: 1px solid rgba(0,0,0,.18); }
  .nav a.current { background: rgba(0,0,0,.12); }

  .panel { left: 79px; top: 180px; width: 825px; height: 924px; background: var(--white); }

  .hero { left: 88px; top: 188px; width: 807px; height: 281px; background: linear-gradient(#9d9a93 0%, #c3beb4 35%, #8a8176 70%, #5a5248 100%); overflow: hidden; }
  .hero-title { position: absolute; left: 19px; top: 165px; font-family: "Signika", sans-serif; font-weight: 600; font-size: 31px; color: var(--white); text-shadow: 0 1px 3px rgba(0,0,0,.4); white-space: nowrap; }
  .hero-arrows { left: 445px; top: 430px; }

  .service { top: 505px; width: 224px; }
  .service h2 { font-family: "Oxygen", sans-serif; font-weight: 400; font-size: 14px; color: #444; border-left: 3px solid var(--blue); padding-left: 9px; line-height: 24px; }
  .service hr { border: 0; border-top: 1px solid var(--rule); margin-top: 13px; width: 222px; }
  .service-photo { margin-top: 18px; width: 222px; height: 99px; border: 1px solid #ddd; box-shadow: 0 1px 3px rgba(0,0,0,.15); padding: 5px; background: var(--white); }
  .service-photo span { display: block; width: 100%; height: 100%; }
  .service p { font-family: "Arimo", sans-serif; font-size: 10px; line-height: 18px; color: var(--text); margin-top: 13px; letter-spacing: -0.1px; }
  .btn { display: block; width: 76px; margin: 12px 2px 0 auto; background: var(--blue); color: var(--white); font-family: "Arimo", sans-serif; font-size: 11px; text-align: center; line-height: 23px; text-decoration: none; }

  .welcome { left: 117px; top: 822px; width: 460px; }
  .section-title { font-family: "Oxygen", sans-serif; font-weight: 400; font-size: 22px; color: var(--blue); }
  .welcome .lead { color: var(--blue); font-size: 11px; line-height: 19px; margin-top: 7px; letter-spacing: -0.1px; }
  .welcome .body { font-size: 11px; line-height: 19px; margin-top: 8px; color: var(--text); letter-spacing: -0.1px; }
  .welcome .body + .body { margin-top: 5px; }

  .news { left: 641px; top: 822px; width: 230px; }
  .news-item { padding: 12px 0 12px 2px; }
  .news-item + .news-item { border-top: 1px dotted #bbb; }
  .news-item h3 { font-family: "Arimo", sans-serif; font-weight: 400; font-size: 10.5px; color: var(--blue-deep); white-space: nowrap; }
  .news-item time { display: block; font-family: "Arimo", sans-serif; font-size: 9.5px; color: #777; margin-top: 9px; }
  .news-item p { font-size: 10.5px; line-height: 18px; color: var(--text-soft); margin-top: 5px; letter-spacing: -0.15px; }

  .footer-links { left: 79px; top: 1126px; font-family: "Signika", sans-serif; font-weight: 300; font-size: 11px; color: #555; }
  .footer-links span { color: #bbb; margin: 0 5px; }
  .copyright { left: 79px; top: 1154px; font-family: "Signika", sans-serif; font-weight: 300; font-size: 11px; color: #555; }
  .social { left: 823px; top: 1141px; display: flex; gap: 6px; }
  .social span { width: 20px; height: 20px; border-radius: 2px; display: block; }
</style>
</head>
<body>
  <div class="top-band"></div>

  <div class="abs brand">
    <span class="brand-mark"></span>
    <div class="brand-name">Okabe Law Group, LLP</div>
    <div class="brand-tag">Attorneys at Law</div>
  </div>

  <div class="abs call">
    <div class="call-label">Call today</div>
    <div class="call-number">+71 02 5550 1426</div>
  </div>
  <svg class="abs call-icon" width="22" height="32" viewBox="0 0 22 32" aria-hidden="true">
    <path d="M6 2 L10 8 L7 11 C8 16 11 20 14 23 L17 20 L21 25 L17 30 C9 28 2 17 2 7 Z" fill="#fff"/>
  </svg>

  <div class="abs search">Search
    <svg width="16" height="16" viewBox="0 0 16 16" aria-hidden="true"><circle cx="6.5" cy="6.5" r="4.5" fill="none" stroke="#999" stroke-width="2"/><line x1="10" y1="10" x2="14.5" y2="14.5" stroke="#999" stroke-width="2.4"/></svg>
  </div>

  <div class="panel abs"></div>

  <nav class="abs nav">
    <a class="current" href="#" style="width:91px">HOME</a>
    <a href="#" style="width:129px">ABOUT OLG</a>
    <a href="#" style="width:156px">PRACTICE AREAS</a>
    <a href="#" style="width:100px">LINKS</a>
    <a href="#" style="width:120px">CONTACT</a>
  </nav>

  <div class="abs hero" role="img" aria-label="Photo of a city skyline with high-rise towers under a hazy sky">
    <div class="hero-title">We hold the national quality standards</div>
  </div>
  <svg class="abs hero-arrows" width="80" height="40" viewBox="0 0 80 40" aria-label="Slide controls">
    <path d="M1 40 A39 39 0 0 1 79 40 Z" fill="#fff"/>
    <line x1="40" y1="10" x2="40" y2="36" stroke="#ddd"/>
    <path d="M28 18 L23 23 L28 28" fill="none" stroke="#111" stroke-width="3"/>
    <path d="M52 18 L57 23 L52 28" fill="none" stroke="#111" stroke-width="3"/>
  </svg>

  <section class="abs service" style="left:118px">
    <h2>BUSINESS</h2><hr>
    <div class="service-photo"><span role="img" aria-label="Photo of two people shaking hands" style="background:linear-gradient(135deg,#7fa9d6,#c9d6e2 50%,#6b6f78)"></span></div>
    <p>Dipisicing elit sed do eidolorem magna aliqua. Ut enim adnostru exercitation des ullam Dipisicing el it sed do eidolorem magna aliqua magna.</p>
    <a class="btn" href="#">READ MORE</a>
  </section>
  <section class="abs service" style="left:374px">
    <h2>CORPORATE</h2><hr>
    <div class="service-photo"><span role="img" aria-label="Photo of business people walking through an office lobby" style="background:linear-gradient(90deg,#8b7e6c,#cfc8bb 45%,#e08a3c 75%,#7a6f66)"></span></div>
    <p>Dipisicing elit sed do eidolorem magna aliqua. Ut enim adnostru exercitation des ullam Dipisicing el it sed do eidolorem magna aliqua magna.</p>
    <a class="btn" href="#">READ MORE</a>
  </section>
  <section class="abs service" style="left:629px">
    <h2>LITIGATION MATTERS</h2><hr>
    <div class="service-photo"><span role="img" aria-label="Photo of hands signing a document with a pen" style="background:linear-gradient(135deg,#3a4a6a,#b9c3d6 50%,#e6eaf2)"></span></div>
    <p>Dipisicing elit sed do eidolorem magna aliqua. Ut enim adnostru exercitation des ullam Dipisicing el it sed do eidolorem magna aliqua magna.</p>
    <a class="btn" href="#">READ MORE</a>
  </section>

  <section class="abs welcome">
    <h1 class="section-title">Welcome to Our Website Mainpage</h1>
    <p class="lead">Okabe Law Group, LLP provides quality legal representation to corporate as well as individual clients in the areas of business, corporate, securities, products liability.</p>
    <p class="body">Our attorneys are committed to providing zealous advocacy in litigation, as well as creative approaches to difficult challenges that face our business clients. Our goal is to provide the highest level of representation and personal service to each and every client, and to meet and exceed each client's expectations. We take the time to explore and explain all viable options and keep our clients informed at every step of their legal matter.</p>
    <p class="body">We encourage you to contact us to discuss the development of a professional relationship. If you seek a firm that is experienced and committed to representing your best interests, then look no further.</p>
  </section>

  <section class="abs news">
    <h2 class="section-title">Latest News</h2>
    <article class="news-item">
      <h3>TYPI NON HABENT CLARITATEM INSITAM;</h3>
      <time>26/11/2013</time>
      <p>Typi non habent claritatem insitam; est usislegen tis in iis qui facit eorum claritatem Investigatnes.</p>
    </article>
    <article class="news-item">
      <h3>TYPI NON HABENT CLARITATEM INSITAM;</h3>
      <time>26/11/2013</time>
      <p>Typi non habent claritatem insitam; est usislegen tis in iis qui facit eorum claritatem Investigatnes.</p>
    </article>
  </section>

  <div class="abs footer-links">Home<span>|</span>About OLG<span>|</span>Practice Areas<span>|</span>Links<span>|</span>Contact</div>
  <div class="abs copyright">Copyright &copy; 2013 &nbsp; Northlight Studio. &nbsp; All rights reserved.</div>
  <div class="abs social" aria-label="Social links">
    <span style="background:#3b5998"></span>
    <span style="background:#39a9e0"></span>
  </div>
</body>
</html>
```